Personal Business Card design contest for freelance work

Include

Brenvola.net/in/DanielMWhitacre (as URL and/or QR Code)
Daniel Whitacre
(555) 218-9034
DanielMWhitacre@Pelmora.com
Houston, TX

Industry/Entity Type

Business

```html
<!DOCTYPE html>
<html lang="en">
<head>
<meta charset="utf-8">
<title>Daniel Whitacre Business Card</title>
<link rel="stylesheet" href="https://fonts.googleapis.com/css2?family=Crimson+Text:wght@400;700&display=swap">
<style>
  :root {
    --page-bg: #e9e9e7;
    --card-front: #fbfbfb;
    --card-back: #000000;
    --ink: #1a1a1a;
    --accent-blue: #4aa3e0;
    --art-front-top: #d8d4d0;
    --art-front-bottom: #c2c6c9;
    --art-back-top: #2a2a2c;
    --art-back-bottom: #1c2326;
  }
  * { margin: 0; padding: 0; box-sizing: border-box; }
  html, body {
    width: 1200px;
    height: 844px;
    overflow: hidden;
    background: var(--page-bg);
  }
  .canvas {
    width: 1200px;
    height: 844px;
    display: flex;
    align-items: center;
    justify-content: center;
    gap: 40px;
  }
  .card {
    position: relative;
    width: 540px;
    height: 309px;
    box-shadow: 0 6px 18px rgba(0,0,0,0.18);
    font-family: "Crimson Text", Georgia, serif;
  }
  .card--front { background: var(--card-front); }
  .card--back { background: var(--card-back); }

  .illustration { position: absolute; }
  .card--front .illustration {
    top: 24px;
    right: 40px;
    width: 116px;
    height: 160px;
    background: linear-gradient(180deg, var(--art-front-top), var(--art-front-bottom));
  }
  .card--back .illustration {
    top: 58px;
    left: 50%;
    transform: translateX(-50%);
    width: 130px;
    height: 190px;
    background: linear-gradient(180deg, var(--art-back-top), var(--art-back-bottom));
  }

  .identity {
    position: absolute;
    left: 38px;
    top: 168px;
  }
  .identity__name {
    font-weight: 700;
    font-size: 23px;
    line-height: 1;
    color: var(--ink);
  }
  .identity__role {
    font-size: 14px;
    color: var(--accent-blue);
    margin-top: 3px;
  }
  .contact {
    position: absolute;
    left: 38px;
    top: 232px;
    font-size: 13.5px;
    line-height: 1.3;
    color: var(--ink);
    white-space: nowrap;
  }
  .contact__label { color: var(--accent-blue); }
  .contact__gap { margin-left: 8px; }
  .contact__web { color: var(--accent-blue); margin-left: 8px; }
</style>
</head>
<body>
  <main class="canvas">
    <section class="card card--front">
      <div class="illustration" role="img" aria-label="Illustrated portrait of the cardholder in a dark suit"></div>
      <div class="identity">
        <h1 class="identity__name">Daniel Whitacre</h1>
        <p class="identity__role">Managing Director</p>
      </div>
      <div class="contact">
        <p>Houston, TX</p>
        <p><span class="contact__label">T:</span>(555) 218-9034 <span class="contact__label contact__gap">F:</span>(555) 218-9034 <span class="contact__label contact__gap">M:</span>(555) 218-9034</p>
        <p>DanielMWhitacre@Pelmora.com <span class="contact__web">Brenvola.net/in/DanielMWhitacre</span></p>
      </div>
    </section>

    <section class="card card--back">
      <div class="illustration" role="img" aria-label="Illustrated portrait of the cardholder in a dark suit"></div>
    </section>
  </main>
</body>
</html>
```